I am looking to create a newly designed website for our national leadership conference which is entitled, "The Harbor of Momentum Leadership Summit". The Harbor of Momentum Leadership Summit is a national conference for student leaders that prepares them for career leadership success. The current website can be seen at www.harborofmomentumleadershipsummit.com.

My goal for the new site is to create a more updated, fresh, hip, and exciting look that appeals to the younger generation while also maintaining are professional appeal. The color should be black, white, and gold. We want there to be live videos played and places to insert pictures for the panels as well.

I look forward to seeing you the new creations.

Requirements
Must have
• Ability to play videos on the home page and throughout the website. Also, make sure that the website shows up clearly on an zTablet.
Nice to have
• Nice look

```html
<!DOCTYPE html>
<html lang="en">
<head>
<meta charset="utf-8">
<title>Speaker Profiles – Harbor of Momentum</title>
<link href="https://fonts.googleapis.com/css2?family=Roboto:wght@300;400;500;700&display=swap" rel="stylesheet">
<style>
:root{
  --gold:#b58a3c;
  --gold-light:#d1a859;
  --gold-dark:#a07a30;
  --ink:#1c1c1c;
  --text:#555;
  --muted:#8a8a8a;
  --rule:#dcdcdc;
  --nav-top:#3a3a3a;
  --nav-bottom:#141414;
  --footer:#2b2b2b;
  --white:#fff;
}
*{box-sizing:border-box;margin:0;padding:0}
html,body{width:1200px;height:2211px;overflow:hidden;background:var(--white)}
body{font-family:'Roboto',sans-serif;color:var(--text);position:relative}
a{color:inherit;text-decoration:none}

.site-header{position:absolute;left:0;top:0;width:1200px;height:125px}
.follow{position:absolute;left:75px;top:52px;display:flex;align-items:center;gap:10px;font-size:11px;font-weight:500;color:var(--ink)}
.social{display:flex;gap:4px}
.social span{width:28px;height:28px;background:#9a9a9a;display:block}
.brand{position:absolute;left:450px;width:300px;top:22px;text-align:center}
.brand-mark{width:40px;height:40px;border-radius:50%;background:linear-gradient(#d8b565,#a07a30);margin:0 auto 14px}
.brand-name{font-weight:700;font-size:15px;letter-spacing:2px;color:var(--ink)}
.register-btn{position:absolute;left:904px;top:35px;width:221px;height:51px;border-radius:26px;background:linear-gradient(var(--gold-light),var(--gold-dark));color:var(--white);font-size:21px;font-weight:500;letter-spacing:1px;display:flex;align-items:center;justify-content:center}

.main-nav{position:absolute;left:0;top:125px;width:1200px;height:61px;background:linear-gradient(var(--nav-top),var(--nav-bottom))}
.main-nav ul{list-style:none;position:absolute;left:75px;top:0;height:61px;display:grid;grid-template-columns:98px 107px 185px 136px 165px 219px 140px}
.main-nav li{display:flex;align-items:center;justify-content:center;color:var(--white);font-size:14px;font-weight:500;white-space:nowrap}
.main-nav li.active{background:linear-gradient(var(--gold-light),var(--gold-dark))}

.breadcrumb{position:absolute;left:81px;top:219px;font-size:11px;color:var(--muted)}
.breadcrumb .current{color:var(--gold)}
.breadcrumb .sep{margin:0 6px}
.rule{position:absolute;left:75px;width:1050px;height:1px;background:var(--rule)}

.section-title{position:absolute;left:75px;top:295px;display:flex;align-items:center;gap:19px}
.section-title .dot{width:55px;height:41px;border-radius:50%;background:linear-gradient(#d8b565,#8a6a2a)}
.section-title h1{font-size:23px;font-weight:400;color:var(--ink);letter-spacing:.5px}
.section-title h1 span{color:var(--gold)}

.speaker{position:absolute;left:75px;width:1050px;border-bottom:1px solid var(--rule)}
.speaker:last-of-type{border-bottom:none}
.speaker .photo{position:absolute;left:0;top:29px;width:204px;height:184px;border-radius:26px}
.speaker .bio{position:absolute;left:235px;top:29px;width:815px}
.speaker h2{font-size:16px;font-weight:500;color:var(--gold);letter-spacing:.5px;margin:4px 0 11px}
.speaker p{font-size:13.3px;font-weight:300;line-height:24px;margin-bottom:8px}
.read-more{position:absolute;left:235px;width:129px;height:38px;border-radius:19px;background:linear-gradient(#3a3a3a,#111);color:var(--white);font-size:13px;font-weight:500;display:flex;align-items:center;justify-content:center}

.site-footer{position:absolute;left:0;top:2027px;width:1200px;height:184px;background:var(--footer)}
.footer-nav{position:absolute;left:75px;top:56px;display:flex;gap:30px;list-style:none;font-size:12px;font-weight:500;color:var(--white)}
.legal{position:absolute;left:75px;top:101px;font-size:11px;color:#9a9a9a;line-height:20px}
.footer-brand{position:absolute;left:936px;top:48px;width:200px;text-align:center}
.footer-brand .brand-mark{width:36px;height:36px;background:#6e6e6e;margin-bottom:14px}
.footer-brand .brand-name{color:#8a8a8a;font-size:15px}
</style>
</head>
<body>

<header class="site-header">
  <div class="follow">FOLLOW US
    <div class="social"><span></span><span></span><span></span><span></span><span></span></div>
  </div>
  <div class="brand">
    <div class="brand-mark"></div>
    <div class="brand-name">HARBOR OF MOMENTUM</div>
  </div>
  <a class="register-btn" href="#">REGISTER NOW</a>
</header>

<nav class="main-nav">
  <ul>
    <li>HOME</li><li>ABOUT</li><li>CONFERENCE PROGRAMS</li><li>REGISTER</li>
    <li class="active">SPEAKER PROFILES</li><li>REGIONAL CONFERENCES</li><li>CONTACT</li>
  </ul>
</nav>

<div class="breadcrumb">HOME<span class="sep">»</span><span class="current">SPEAKER PROFILE</span></div>
<div class="rule" style="top:255px"></div>

<div class="section-title"><div class="dot"></div><h1>KEYNOTE <span>SPEAKERS</span></h1></div>

<article class="speaker" style="top:332px;height:327px">
  <div class="photo" role="img" aria-label="Portrait photo of Maya Ellison" style="background:linear-gradient(135deg,#7a6a5e,#3a2b26)"></div>
  <div class="bio">
    <h2>MAYA ELLISON</h2>
    <p>As one of the nation's premier campus keynote speakers, Maya Ellison uses public speaking as a platform for change. She is the Executive Director of Rising Leaders Forward, Inc., a leadership development company, specializing in collegiate programming in leadership, women, career skills and the African American experience.</p>
    <p>An enthusiastic speaker with a commitment to creating a successful collegiate experience, Maya is a highly regarded presenter, which is why her keynotes have become favorites among universities, associations, and leadership conferences from coast to coast. She wants to see students expand their opportunities for leadership, solicit greater student involvement, and actively contribute to the transformation and growth of their campus' student development.</p>
  </div>
  <a class="read-more" href="#" style="top:262px">Read More</a>
</article>

<article class="speaker" style="top:659px;height:355px">
  <div class="photo" role="img" aria-label="Portrait photo of Marcus Delaney" style="background:linear-gradient(135deg,#b9b9b5,#4d5866)"></div>
  <div class="bio">
    <h2>MARCUS DELANEY</h2>
    <p>Marcus Delaney is a national speaker, author, entrepreneur and leadership expert who specializes in current issues and effective leadership strategies for emerging and seasoned leaders. For the past six years, Marcus has been a dynamic keynote speaker in 35 states for various leadership conferences, retreats and trainings at high schools, colleges and corporate organizations.</p>
    <p>In addition to speaking and empowering emerging and seasoned leaders for leadership success, Marcus has also written three books, completed an Masters of Arts degree in Organizational Leadership, spoken on a variety of television shows as an expert on issues pertaining to Generation Y and has developed an annual leadership conference that prepares college students and young professionals for executive level leadership positions after graduation.</p>
  </div>
  <a class="read-more" href="#" style="top:281px">Read More</a>
</article>

<article class="speaker" style="top:1014px;height:313px">
  <div class="photo" role="img" aria-label="Portrait photo of Darnell Hayes" style="background:linear-gradient(135deg,#6d6d6d,#1e1e1e)"></div>
  <div class="bio">
    <h2>DARNELL HAYES</h2>
    <p>Darnell Hayes learned the importance of nurturing dreams at an early age after overcoming a difficult childhood. It was the struggle of his childhood that gave him the fuel and created the work ethic necessary to earn a baseball scholarship and graduate from Westridge State University. After graduating, Darnell played two years of professional baseball in Canada, today he is an international speaker, teacher, author and entrepreneur. Darnell has delivered messages for organizations such as Peak Hour Gyms, Northbay Computing, Linewave Telecom, Valley Roads, Medicor Health, The National Athlete Center, Summit Life Insurance, Harvest Mutual, The Healthy Start Foundation and Sunvale Sports Park.</p>
  </div>
  <a class="read-more" href="#" style="top:237px">Read More</a>
</article>

<article class="speaker" style="top:1327px;height:349px">
  <div class="photo" role="img" aria-label="Portrait photo of Brian Whitfield" style="background:linear-gradient(135deg,#b98a4a,#151515)"></div>
  <div class="bio">
    <h2>BRIAN WHITFIELD</h2>
    <p>Brian Whitfield is known worldwide as The Relationship Coach. He has been honored thirteen times as The National Speaker of the Year— 10 times by Campus Events Journal and 3 times by The National Council for Student Programs and was honored as the 2011 National Entertainer of the Year! He is a highly sought after speaker, author, entertainer, radio and television personality.</p>
    <p>Brian received his B.S. in Speech Pathology and Audiology ('83) and his Master of Arts in College Student Personnel ('85) from Greenfield State University (GSU). His book, Building Bonds That Last, has completed its second printing run, and his previous works, Connect Smart! and 101 Great Conversations are well respected and continue to impact lives worldwide.</p>
  </div>
  <a class="read-more" href="#" style="top:265px">Read More</a>
</article>

<article class="speaker" style="top:1676px;height:351px">
  <div class="photo" role="img" aria-label="Portrait photo of Travis Lindgren" style="background:linear-gradient(135deg,#8a4a22,#2a1a12)"></div>
  <div class="bio">
    <h2>TRAVIS LINDGREN</h2>
    <p>Since 1998, Travis Lindgren has been helping colleges and universities develop their student leaders and increase retention rates by delivering life-changing programs that he has shared in 47 states, Singapore, Hong Kong, Canada and the Bahamas. With a 78% rate of repeat bookings, Travis has become an integral part of orientations, retreats, and leadership series on campuses.</p>
    <p>Travis is the co-author of: "Campus Success Keys: What Lectures Leave Out" as well as a contributing author to numerous other books on success and leadership for college students. His college experience as a Delta Rho Fraternity member and a collegiate Division 1 gymnast, taught him a lot about academic and personal success and relating to the college audience. Travis has appeared on Public Voice Radio and was featured in Nation Daily.</p>
  </div>
  <a class="read-more" href="#" style="top:262px">Read More</a>
</article>

<footer class="site-footer">
  <ul class="footer-nav">
    <li>HOME</li><li>ABOUT</li><li>CONFERENCE</li><li>REGISTER</li><li>TESTIMONIALS</li><li>Y FACTOR</li><li>VIDEOS</li><li>CONTACT</li>
  </ul>
  <div class="legal">Copyright © 2015. Company Name All Right Reserved<br>Privacy Policy &nbsp;|&nbsp; Term &amp; Conditions</div>
  <div class="footer-brand">
    <div class="brand-mark"></div>
    <div class="brand-name">HARBOR OF MOMENTUM</div>
  </div>
</footer>

</body>
</html>
```